Accounting firm needing business card / letterhead designed
Marcus L. Trenholm, CPA
marcus@veltrowledger.com
www.veltrowledger.com
842 E Alder Ave Marlow Bend, WI 43827
419-562-0974

```html
<!DOCTYPE html>
<html lang="en">
<head>
<meta charset="utf-8">
<title>Veltrow Ledger – Business Card</title>
<link href="https://fonts.googleapis.com/css2?family=Roboto:wght@400;500;700&family=Roboto+Condensed:wght@700&display=swap" rel="stylesheet">
<style>
  :root {
    --navy: #23205e;
    --green: #86bd3c;
    --paper: #f4f4f4;
    --white: #ffffff;
    --backdrop: #e4e4e4;
  }
  html, body {
    margin: 0;
    width: 1200px;
    height: 960px;
    overflow: hidden;
    background: var(--backdrop);
    font-family: "Roboto", Arial, sans-serif;
  }
  p { margin: 0; }
  .canvas { position: relative; width: 1200px; height: 960px; }
  .card {
    position: absolute;
    width: 600px;
    height: 343px;
    overflow: hidden;
    box-shadow: 0 2px 4px rgba(0,0,0,0.25);
  }
  .card-front { left: 314px; top: 113px; background: var(--paper); }
  .card-back { left: 311px; top: 472px; background: var(--green); }
  .diagonal { position: absolute; inset: 0; }
  .brand-name {
    position: absolute;
    font-weight: 700;
    white-space: nowrap;
    line-height: 1;
  }
  .card-front .brand-name {
    left: 54px; top: 68px;
    font-size: 22px; letter-spacing: 1.5px;
    color: var(--navy);
  }
  .card-back .brand-name {
    left: 0; right: 0; top: 136px; text-align: center;
    font-size: 36px; letter-spacing: 3px; color: var(--white);
  }
  .contact {
    position: absolute;
    right: 36px;
    top: 164px;
    text-align: right;
    color: var(--white);
    font-size: 14.5px;
    line-height: 18px;
  }
  .contact-name {
    font-family: "Roboto Condensed", "Arial Narrow", sans-serif;
    font-weight: 700;
    font-size: 21px;
    line-height: 26px;
    color: var(--green);
    margin-bottom: 12px;
  }
  .address { margin-bottom: 9px; }
  .line { display: flex; justify-content: flex-end; align-items: center; gap: 8px; height: 19.5px; }
  .icon { width: 13px; height: 13px; fill: var(--green); flex: none; }
  .back-web {
    position: absolute; left: 0; right: 0; top: 281px;
    line-height: 18px;
    text-align: center; color: var(--white);
    font-size: 14.5px; letter-spacing: 5.5px;
  }
</style>
</head>
<body>
<div class="canvas">
  <section class="card card-front">
    <svg class="diagonal" viewBox="0 0 600 343" width="600" height="343" aria-hidden="true">
      <polygon points="405,0 413,0 198,343 190,343" fill="var(--green)"/>
      <polygon points="417,0 600,0 600,343 202,343" fill="var(--navy)"/>
    </svg>
    <p class="brand-name">VELTROW LEDGER</p>
    <div class="contact">
      <p class="contact-name">Marcus L. Trenholm, CPA</p>
      <p class="address">842 E Alder Ave<br>Marlow Bend, WI 43827</p>
      <div class="line">608-562-0974
        <svg class="icon" viewBox="0 0 16 16"><path d="M3.5 1l2.5 3-1.5 2c1 2 3 4 5 5l2-1.5 3 2.5-1.5 2.5C8 15 1 8 1 2.5z"/></svg>
      </div>
      <div class="line">marcus@veltrowledger.com
        <svg class="icon" viewBox="0 0 16 16"><rect x="1" y="3" width="14" height="10"/><path d="M1.5 3.5l6.5 5 6.5-5" stroke="var(--navy)" stroke-width="1.3" fill="none"/></svg>
      </div>
      <div class="line">www.veltrowledger.com
        <svg class="icon" viewBox="0 0 16 16"><circle cx="8" cy="8" r="7"/><path d="M1 8h14M8 1c-3 4-3 10 0 14M8 1c3 4 3 10 0 14" stroke="var(--navy)" stroke-width="1" fill="none"/></svg>
      </div>
    </div>
  </section>

  <section class="card card-back">
    <p class="brand-name">VELTROW LEDGER</p>
    <p class="back-web">www.veltrowledger.com</p>
  </section>
</div>
</body>
</html>
```